Real Estate Business Card

On the front side I want to have my info, my brokerage info.
On the back side I want have my complany’s logo, website and Facebook link. I will provide all this once I select a design.

I would like to see Black background and gold text, Dark Blue and gold text and White and blue text designs

Font styles to use
Sans Serif
Script

```html
<!DOCTYPE html>
<html lang="en">
<head>
<meta charset="utf-8">
<title>Harborline Realty – Business Cards</title>
<link href="https://fonts.googleapis.com/css2?family=Cinzel:wght@600&family=Open+Sans:wght@400;600&display=swap" rel="stylesheet">
<style>
  :root {
    --backdrop: #121212;
    --card: #1b1b1b;
    --gold: #dcae2a;
    --ink-light: #f2f2f2;
    --rule: #3a3a3a;
  }
  * { margin: 0; padding: 0; box-sizing: border-box; }
  html, body {
    width: 1200px; height: 900px; overflow: hidden;
    background: var(--backdrop);
  }
  .canvas { position: relative; width: 1200px; height: 900px; }

  .card {
    position: absolute;
    width: 560px; height: 320px;
    background: var(--card);
    border-radius: 22px;
    box-shadow: 0 18px 40px rgba(0,0,0,.6);
    font-family: "Open Sans", Arial, sans-serif;
    color: var(--ink-light);
  }
  .card--back { left: 80px; top: 90px; }
  .card--front { left: 560px; top: 490px; }

  .brand {
    font-family: "Cinzel", "Times New Roman", serif;
    font-weight: 600;
    color: var(--gold);
    text-align: center;
    line-height: 1;
  }
  .brand__main { display: block; font-size: 44px; letter-spacing: 1px; }
  .brand__sub { display: block; font-size: 15px; letter-spacing: 7px; margin-top: 8px; }

  .card--back .brand { position: absolute; left: 0; right: 0; top: 102px; }
  .card--back .social-link {
    position: absolute; left: 0; right: 0; top: 236px;
    text-align: center; font-size: 15px;
  }

  .card--front .brand { position: absolute; right: 40px; top: 46px; }
  .card--front .brand__main { font-size: 36px; }
  .card--front .brand__sub { font-size: 13px; letter-spacing: 6px; }

  .divider {
    position: absolute; left: 190px; right: 24px; top: 150px;
    height: 1px; background: var(--rule);
  }

  .person { position: absolute; left: 34px; top: 168px; }
  .person__name {
    font-family: "Cinzel", "Times New Roman", serif;
    font-weight: 600; color: var(--gold);
    font-size: 22px; letter-spacing: 1px;
  }
  .person__title { font-size: 15px; margin-top: 2px; }

  .contacts { list-style: none; position: absolute; left: 34px; top: 222px; }
  .contacts li {
    display: flex; align-items: center; gap: 8px;
    font-size: 15px; line-height: 21px;
  }
  .contacts svg { width: 13px; height: 13px; fill: var(--gold); flex: none; }

  .office { position: absolute; right: 34px; top: 182px; text-align: right; font-size: 14px; line-height: 20px; }
  .office__web { color: var(--gold); margin-bottom: 8px; }
</style>
</head>
<body>
<main class="canvas">

  <section class="card card--back" aria-label="Card back">
    <div class="brand">
      <span class="brand__main">HARBORLINE</span>
      <span class="brand__sub">REALTY</span>
    </div>
    <p class="social-link">www.harborline.com/community</p>
  </section>

  <section class="card card--front" aria-label="Card front">
    <div class="brand">
      <span class="brand__main">HARBORLINE</span>
      <span class="brand__sub">REALTY</span>
    </div>
    <div class="divider"></div>

    <div class="person">
      <p class="person__name">DELWYN MARSH</p>
      <p class="person__title">Managing Director</p>
    </div>

    <ul class="contacts">
      <li>
        <svg viewBox="0 0 16 16" aria-hidden="true"><path d="M3 1h3l1.5 4-2 1.2a9 9 0 0 0 4.3 4.3L11 8.5l4 1.5v3a2 2 0 0 1-2 2A12 12 0 0 1 1 3a2 2 0 0 1 2-2z"/></svg>
        055-210 384 617
      </li>
      <li>
        <svg viewBox="0 0 16 16" aria-hidden="true"><path d="M4 0h8a1 1 0 0 1 1 1v14a1 1 0 0 1-1 1H4a1 1 0 0 1-1-1V1a1 1 0 0 1 1-1zm1 2v10h6V2zm3 11a1 1 0 1 0 0 2 1 1 0 0 0 0-2z"/></svg>
        055-210 384 617
      </li>
      <li>
        <svg viewBox="0 0 16 16" aria-hidden="true"><path d="M0 3h16v10H0zm1.5 1.3V12h13V4.3L8 9z"/></svg>
        info@harborline.com
      </li>
      <li>
        <svg viewBox="0 0 16 16" aria-hidden="true"><circle cx="8" cy="8" r="8"/></svg>
        www.harborline.com
      </li>
    </ul>

    <div class="office">
      <p class="office__web">www.harborline.com</p>
      <p>4821, Quayside Avenue Here</p>
      <p>Westmere Bay, 204519</p>
    </div>
  </section>

</main>
</body>
</html>
```